Yacht, Boats, Watersports company needs a redesign of business card

Hello Designers!
We are a Boat dealership company that sells fun in the water, we sell boats, Yachts, Kayaks and also yacht WaterSport toys. We are looking to redesign our business cards in to something a little bit more sophisticated. in a way that we can make better use of our company colors. I'm attaching a zipped file containing the company 3 sets of company logo which one is an horizontal another one is a vertical and also a chromed 3d logo. Also is included two set of business cards that we use and also some designs that i think it's interesting. We use PMS 2026c Orange and PMS 7687C Blue. I would like to see at least two different options with the orange as accent and also using blue as an accent color. It's really important for the business cards to have a font option and size that is legible to most people. Our current website is wwww.coralpennant.com. Please visit if you want to have a better feeling of the Boat dealership
You can send Single sided or double side options. We are now using single sided but we may be open for a double side option if we really like the design.
Target Market(s)
Marine, boat sales, yacht sales, water toys sales/
Contact Information for Business Card
Name: Dale Whitcombe
Address: 212 North Fenwick Lane,
Marlin Cove, FL 33920
Phone: 954-731-8842
Fax: 954:731-8843
Cell: 954-382-1490
Email: dw@coralpennant.com
Website: coralpennant.com
Requirements
Must have
- the current information of the business card provided.
logo
use the PMS Colors
Nice to have
- a touch of elegance and sophistication but simple
Should not have
- should not have any typography that is hard to read, the card should be simple but yet sophisticated.

```html
<!DOCTYPE html>
<html lang="en">
<head>
<meta charset="utf-8">
<title>Coral Pennant Marine Center – Business Card</title>
<link rel="stylesheet" href="https://fonts.googleapis.com/css2?family=Poppins:wght@400;600&family=Oswald:wght@500&display=swap">
<style>
  :root {
    --page: #e9ebee;
    --card: #ffffff;
    --brand-blue: #1f6db4;
    --brand-orange: #f28a22;
    --text-grey: #4a4a4a;
    --back-text: #d6ecff;
  }
  * { margin: 0; padding: 0; box-sizing: border-box; }
  html, body {
    width: 1125px; height: 1200px; overflow: hidden;
    background: var(--page);
    font-family: "Poppins", sans-serif;
  }
  .card {
    position: absolute; left: 150px; width: 825px; height: 471px;
    background: var(--card);
    box-shadow: 0 4px 14px rgba(0,0,0,.18);
    overflow: hidden;
  }
  .card--front { top: 106px; }
  .card--back { top: 639px; background: var(--brand-blue); }

  .edge-bar { position: absolute; left: 0; width: 17px; }
  .edge-bar--orange { top: 0; height: 175px; background: var(--brand-orange); }
  .edge-bar--blue { top: 178px; bottom: 0; background: var(--brand-blue); }

  .brand-name {
    position: absolute; left: 49px; top: 60px;
    font-weight: 600; font-size: 24px; letter-spacing: 1px;
    color: var(--brand-blue);
  }
  .brand-rule {
    position: absolute; left: 49px; top: 103px; width: 302px; height: 3px;
    background: var(--brand-orange);
  }

  .contact {
    position: absolute; left: 49px; top: 232px;
    color: var(--text-grey); font-size: 18px; line-height: 23px;
  }
  .contact__address { margin-bottom: 14px; }
  .contact__line { display: flex; align-items: center; gap: 11px; height: 23.5px; }
  .contact__icon { width: 16px; height: 16px; fill: var(--brand-blue); flex: none; }

  .person-name {
    position: absolute; right: 48px; top: 354px;
    font-family: "Oswald", sans-serif; font-weight: 500; font-size: 39px;
    letter-spacing: .5px; text-transform: uppercase; line-height: 1.2;
  }
  .person-name__first { color: var(--brand-blue); }
  .person-name__last { color: var(--brand-orange); }

  .back-mark {
    position: absolute; left: 50%; top: 120px; transform: translateX(-50%);
    width: 122px; height: 122px; border-radius: 50%;
    border: 5px solid #4aa3ff;
  }
  .back-name {
    position: absolute; left: 0; right: 0; top: 268px; text-align: center;
    font-weight: 600; font-size: 34px; letter-spacing: 2px;
    color: var(--back-text);
  }
</style>
</head>
<body>
  <section class="card card--front" aria-label="Card front">
    <div class="edge-bar edge-bar--orange"></div>
    <div class="edge-bar edge-bar--blue"></div>

    <div class="brand-name">CORAL PENNANT</div>
    <div class="brand-rule"></div>

    <div class="contact">
      <p class="contact__address">212 North Fenwick Lane<br>Marlin Cove, FL 33920</p>
      <p class="contact__line">
        <svg class="contact__icon" viewBox="0 0 16 16" aria-hidden="true"><path d="M3.5 1.5l2.5 0 1 3.5-1.6 1.2a8 8 0 0 0 4.4 4.4L11 9l3.5 1v2.5c0 1-1 2-2 2C6.5 14.5 1.5 9.5 1.5 3.5c0-1 1-2 2-2z"/></svg>
        954-731-8842</p>
      <p class="contact__line">
        <svg class="contact__icon" viewBox="0 0 16 16" aria-hidden="true"><path d="M4.5 1h7a1 1 0 0 1 1 1v12a1 1 0 0 1-1 1h-7a1 1 0 0 1-1-1V2a1 1 0 0 1 1-1zm.8 2v9h5.4V3zM8 12.6a.8.8 0 1 0 0 1.6.8.8 0 0 0 0-1.6z"/></svg>
        954-382-1490</p>
      <p class="contact__line">
        <svg class="contact__icon" viewBox="0 0 16 16" aria-hidden="true"><path d="M4 1h7l1 1v3H4zM2 6h12a1 1 0 0 1 1 1v5H1V7a1 1 0 0 1 1-1zm2 7h8v2H4z"/></svg>
        954-731-8843</p>
      <p class="contact__line">
        <svg class="contact__icon" viewBox="0 0 16 16" aria-hidden="true"><path d="M1 4h14v1L8 9.5 1 5zm0 2.4l7 4.4 7-4.4V13H1z"/></svg>
        dw@coralpennant.com</p>
      <p class="contact__line">
        <svg class="contact__icon" viewBox="0 0 16 16" aria-hidden="true"><path d="M8 1a7 7 0 1 0 0 14A7 7 0 0 0 8 1zm-1 2.2c-.5 1-1.6 1.4-1.6 2.5 0 1 1.2 1.2 1.6 2 .4.9-.3 2 .4 2.8.6.7.9 1.6.8 2.4A5.5 5.5 0 0 1 3 5a5.5 5.5 0 0 1 4-1.8zm3.2 1c1.6.8 2.8 2.6 2.8 4.6 0 1-.3 2-.8 2.8-.4-.8-1.3-1-1.6-1.9-.3-1 .6-2-.3-2.8-.6-.5-1.6-.3-1.6-1.3 0-.6.7-1 1.5-1.4z"/></svg>
        coralpennant.com</p>
    </div>

    <h1 class="person-name"><span class="person-name__first">Dale</span> <span class="person-name__last">Whitcombe</span></h1>
  </section>

  <section class="card card--back" aria-label="Card back">
    <div class="back-mark"></div>
    <div class="back-name">CORAL PENNANT</div>
  </section>
</body>
</html>
```